Membership Based Medical Practice Website

We need a functioning website for a new Membership based medical practice. There will be an enrollment fee and a monthly fee. We would like to see designs that are modern, simple. Should use neutral light colors. Examples of sites we like are www.kellanmoorclinic.com and https://fernholtcare.com/ We also have a link that when "Join Now" is clicked it will go to the signup website.

Target Market(s)

Gay Men, local population, Age group 20 to 60's.

Industry/Entity Type

Medical

Coding

Coded - Design and coding required

Number of Pages Required

5+ page

Font styles to use
Sans Serif

Colors
ffffff
cee9f5
ecf7fb
cfeae6
edf8f6
aaaaaa
e9e9e9
dbdbdb
fff3d1

Requirements
Must have
• Logo and header on every page. Clean, simple design, clear content, mobile compatible.
• Must use Wordpress
Nice to have
• Ideas should come from kellanmoorclinic.com
• Easy to read
Should not have
• Generic patient pictures, bold colors.
• Should not copy from above websites.

```html
<!DOCTYPE html>
<html lang="en">
<head>
<meta charset="utf-8">
<title>Larkfield Infectious Disease Specialists</title>
<link href="https://fonts.googleapis.com/css2?family=Montserrat:wght@300;400;500;600&family=Lato:wght@400;700&display=swap" rel="stylesheet">
<style>
:root{
  --white:#ffffff;
  --ink:#3a3a3a;
  --ink-soft:#555555;
  --muted:#aaaaaa;
  --rule:#e9e9e9;
  --accent:#4fb0d8;
  --tick:#6fbfe0;
  --sky:#cee9f5;
  --mint:#e8f6f2;
  --mint-btn:#cfeae6;
  --gold:#d8b24a;
  --footer:#f4f4f4;
}
*{box-sizing:border-box;margin:0;padding:0}
html,body{width:1200px;height:3237px;overflow:hidden}
body{position:relative;background:var(--white);font-family:'Lato',sans-serif;color:var(--ink)}
.abs{position:absolute}
.center{left:0;width:1200px;text-align:center}

/* header */
.site-header{position:absolute;top:0;left:0;width:1200px;height:112px;background:var(--white);box-shadow:0 1px 4px rgba(0,0,0,.06);z-index:2}
.brand{position:absolute;display:flex;flex-direction:column;align-items:center}
.site-header .brand{left:172px;top:10px;width:152px}
.brand-dot{width:40px;height:40px;border-radius:50%;border:2px solid var(--gold);margin-bottom:22px}
.brand-name{font-family:'Montserrat',sans-serif;font-weight:400;font-size:8.5px;color:var(--ink-soft);line-height:12px;text-transform:uppercase;white-space:nowrap;text-align:center}
.brand-name .word{display:block;letter-spacing:6px;margin-right:-6px}
.nav{position:absolute;top:40px;left:396px;display:flex;align-items:center;font-family:'Montserrat',sans-serif;font-size:14px;letter-spacing:1px;color:var(--ink-soft)}
.nav a{color:inherit;text-decoration:none;margin-right:46px}
.nav .join{margin:0;background:var(--mint-btn);padding:8px 22px;border-radius:18px;color:#2f6f62}

/* hero */
.hero{position:absolute;top:112px;left:0;width:1200px;height:557px;background:linear-gradient(180deg,#b7bcbd 0%,#9aa19c 40%,#5f6b58 62%,#3a3d3a 100%)}
.hero h1{position:absolute;top:258px;left:0;width:1200px;text-align:center;color:var(--white);font-family:'Montserrat',sans-serif;font-weight:500;font-size:34px;line-height:42px;text-shadow:0 1px 3px rgba(0,0,0,.35)}
.hero h1 .line1{letter-spacing:6px}
.dots{position:absolute;top:518px;left:582px;display:flex;gap:6px}
.dots span{width:8px;height:8px;border-radius:50%;background:rgba(255,255,255,.6)}
.dots span:first-child{background:var(--white)}

/* intro */
.mark{position:absolute;top:696px;left:583px;width:34px;height:34px;border-radius:50%;border:2px solid var(--gold)}
.h2{font-family:'Montserrat',sans-serif;font-weight:300;font-size:28px;line-height:33px;color:var(--ink)}
.sub{font-family:'Montserrat',sans-serif;font-weight:300;font-size:19px;color:var(--ink-soft)}
.area-list{position:absolute;list-style:none;width:340px}
.area-list li{height:52px;border-bottom:1px solid var(--rule);display:flex;align-items:center;gap:12px;font-family:'Montserrat',sans-serif;font-size:17px;letter-spacing:.4px;color:var(--accent)}
.area-list li:last-child{border-bottom:none}
.tick{width:16px;height:16px;flex:none}

/* benefits */
.benefits{position:absolute;top:1240px;left:0;width:1200px;height:725px;background:var(--mint)}
.feature{position:absolute;width:200px;text-align:center}
.feature .icon{width:82px;height:82px;border-radius:50%;background:var(--sky);margin:0 auto;display:flex;align-items:center;justify-content:center}
.feature h3{margin-top:20px;font-family:'Montserrat',sans-serif;font-weight:400;font-size:15px;color:var(--ink)}
.feature p{margin-top:12px;font-size:11.5px;line-height:19px;color:var(--ink-soft)}

/* pricing */
.perks{position:absolute;top:2186px;left:172px;list-style:none}
.perks li{height:33px;display:flex;align-items:center;gap:12px;font-family:'Montserrat',sans-serif;font-size:15px;color:var(--ink-soft)}
.btn{position:absolute;top:2378px;left:172px;width:198px;height:36px;border-radius:18px;background:var(--sky);font-family:'Montserrat',sans-serif;font-size:13px;letter-spacing:.5px;color:#2b5a6e;display:flex;align-items:center;justify-content:center;text-decoration:none}
.clock-art{position:absolute;top:2172px;left:782px;width:226px;height:226px;border-radius:50%;background:radial-gradient(circle at 40% 40%,#f4f4f4 0%,#d7dadd 70%,#e9c546 71%,#f1cf4a 100%)}
.photo{position:absolute;top:2300px;left:0;width:1200px;height:598px;background:linear-gradient(180deg,rgba(255,255,255,1) 0%,rgba(250,236,226,1) 25%,#e9b892 55%,#c27c4d 80%,#8a5a3c 100%)}

/* footer */
.site-footer{position:absolute;top:2898px;left:0;width:1200px;height:339px;background:var(--footer)}
.fcol{position:absolute;top:86px;font-size:13px;line-height:24px;color:var(--ink-soft)}
.fcol h4{font-family:'Montserrat',sans-serif;font-weight:600;font-size:16px;color:var(--ink);margin-bottom:8px;display:flex;align-items:center;gap:10px}
.site-footer .brand{left:834px;top:88px;width:192px}
.site-footer .brand-dot{width:56px;height:56px;margin-bottom:26px}
.site-footer .brand-name{font-size:11px;line-height:14px}
.site-footer .brand-name .word{letter-spacing:8px;margin-right:-8px}
.frule{position:absolute;top:270px;left:172px;width:854px;height:1px;background:var(--rule)}
.copy{position:absolute;top:298px;left:172px;font-size:12.5px;color:var(--ink)}
.socials{position:absolute;top:294px;left:908px;display:flex;gap:6px}
.socials span{width:24px;height:24px;border-radius:50%}
.ver{position:absolute;top:312px;left:1110px;font-size:11px;color:var(--muted)}
</style>
</head>
<body>

<header class="site-header">
  <div class="brand"><span class="brand-dot"></span><span class="brand-name"><span class="word">Larkfield</span>Infectious Disease Specialists</span></div>
  <nav class="nav">
    <a href="#">HOME</a><a href="#">SPECIALTIES</a><a href="#">PRICING</a><a href="#">ABOUT US</a><a href="#">FAQ</a><a href="#">BLOG</a><a href="#" class="join">JOIN US</a>
  </nav>
</header>

<section class="hero" role="img" aria-label="Misty countryside road leading through green hills">
  <h1><span class="line1">Specialty Medicine with</span><br>Commitment, Compassion and Care</h1>
  <div class="dots"><span></span><span></span><span></span></div>
</section>

<span class="mark"></span>
<h2 class="abs center h2" style="top:766px">We offer comprehensive treatment of a<br>wide variety of infectious diseases.</h2>
<p class="abs center sub" style="top:852px">Out expertise is in the following area.</p>

<ul class="area-list" style="top:903px;left:230px">
  <li><svg class="tick" viewBox="0 0 16 16"><circle cx="8" cy="8" r="8" fill="var(--tick)"/><path d="M4.5 8.3l2.3 2.2 4.7-4.8" stroke="#fff" stroke-width="1.8" fill="none"/></svg>HIV/PrEP</li>
  <li><svg class="tick" viewBox="0 0 16 16"><circle cx="8" cy="8" r="8" fill="var(--tick)"/><path d="M4.5 8.3l2.3 2.2 4.7-4.8" stroke="#fff" stroke-width="1.8" fill="none"/></svg>Chronic Hepatitis</li>
  <li><svg class="tick" viewBox="0 0 16 16"><circle cx="8" cy="8" r="8" fill="var(--tick)"/><path d="M4.5 8.3l2.3 2.2 4.7-4.8" stroke="#fff" stroke-width="1.8" fill="none"/></svg>Sexually transmitted infections</li>
  <li style="width:420px"><svg class="tick" viewBox="0 0 16 16"><circle cx="8" cy="8" r="8" fill="var(--tick)"/><path d="M4.5 8.3l2.3 2.2 4.7-4.8" stroke="#fff" stroke-width="1.8" fill="none"/></svg>Pre-travel vaccinations and counselling</li>
  <li style="width:420px"><svg class="tick" viewBox="0 0 16 16"><circle cx="8" cy="8" r="8" fill="var(--tick)"/><path d="M4.5 8.3l2.3 2.2 4.7-4.8" stroke="#fff" stroke-width="1.8" fill="none"/></svg>Infections associated with medical devices</li>
</ul>
<ul class="area-list" style="top:903px;left:727px">
  <li><svg class="tick" viewBox="0 0 16 16"><circle cx="8" cy="8" r="8" fill="var(--tick)"/><path d="M4.5 8.3l2.3 2.2 4.7-4.8" stroke="#fff" stroke-width="1.8" fill="none"/></svg>Bone and Joint infections</li>
  <li><svg class="tick" viewBox="0 0 16 16"><circle cx="8" cy="8" r="8" fill="var(--tick)"/><path d="M4.5 8.3l2.3 2.2 4.7-4.8" stroke="#fff" stroke-width="1.8" fill="none"/></svg>Postsurgical infections</li>
  <li><svg class="tick" viewBox="0 0 16 16"><circle cx="8" cy="8" r="8" fill="var(--tick)"/><path d="M4.5 8.3l2.3 2.2 4.7-4.8" stroke="#fff" stroke-width="1.8" fill="none"/></svg>Diabetes related infections</li>
  <li><svg class="tick" viewBox="0 0 16 16"><circle cx="8" cy="8" r="8" fill="var(--tick)"/><path d="M4.5 8.3l2.3 2.2 4.7-4.8" stroke="#fff" stroke-width="1.8" fill="none"/></svg>Tuberculosis</li>
</ul>

<section class="benefits">
  <h2 class="abs center h2" style="top:86px">Less wait, more personal.</h2>
  <p class="abs center sub" style="top:130px">We are not your traditional doctor's office.</p>

  <div class="feature" style="left:167px;top:211px">
    <div class="icon"><svg width="40" height="40" viewBox="0 0 40 40" fill="none" stroke="#333" stroke-width="1.6"><circle cx="20" cy="20" r="13"/><path d="M24 14.5c-1-1.2-2.5-1.6-4-1.6-2.2 0-3.8 1.1-3.8 2.9 0 4 8 2.2 8 6.5 0 1.9-1.8 3.1-4.2 3.1-1.7 0-3.2-.6-4.2-1.8M20 10.5v19"/></svg></div>
    <h3>Straightforward pricing</h3>
    <p>We charge all our patients the same low rate - no surprises.</p>
  </div>
  <div class="feature" style="left:387px;top:211px">
    <div class="icon"><svg width="40" height="40" viewBox="0 0 40 40" fill="none" stroke="#333" stroke-width="1.6"><circle cx="20" cy="20" r="13"/><path d="M20 12v8l5 3"/></svg></div>
    <h3>Available when you are</h3>
    <p>New patient appointments are available within 1 week.</p>
  </div>
  <div class="feature" style="left:607px;top:211px">
    <div class="icon"><svg width="40" height="40" viewBox="0 0 40 40" fill="none" stroke="#333" stroke-width="1.6"><rect x="8" y="10" width="24" height="22" rx="2"/><path d="M8 16h24M14 7v6M26 7v6M13 21h3M19 21h3M25 21h3M13 26h3M19 26h3"/></svg></div>
    <h3>Hassle-free booking</h3>
    <p>Schedule your appointment online at your convenience - no need to call during business hours.</p>
  </div>
  <div class="feature" style="left:828px;top:211px">
    <div class="icon"><svg width="40" height="40" viewBox="0 0 40 40" fill="none" stroke="#333" stroke-width="1.6"><path d="M20 31s-11-6.5-11-14a5.5 5.5 0 0 1 11-1.5A5.5 5.5 0 0 1 31 17c0 7.5-11 14-11 14z"/></svg></div>
    <h3>Devoted care</h3>
    <p>We schedule enough time at each visit to make sure all of your questions are answered.</p>
  </div>

  <div class="feature" style="left:167px;top:437px">
    <div class="icon"><svg width="40" height="40" viewBox="0 0 40 40" fill="none" stroke="#333" stroke-width="1.6"><path d="M20 33s-9-9.5-9-16a9 9 0 0 1 18 0c0 6.5-9 16-9 16z"/><circle cx="20" cy="17" r="3.5"/></svg></div>
    <h3>Within your reach</h3>
    <p>Follow-up appointments may be done by video chat for your convenience.</p>
  </div>
  <div class="feature" style="left:387px;top:437px">
    <div class="icon"><svg width="40" height="40" viewBox="0 0 40 40" fill="none" stroke="#333" stroke-width="1.6"><path d="M16 8h8M17 8v10l-7 12a2 2 0 0 0 1.7 3h16.6a2 2 0 0 0 1.7-3l-7-12V8M13 25h14"/></svg></div>
    <h3>Save on lab costs</h3>
    <p>If paying upfront for labs, we offer discounted pricing of up to 90% off standard rates.</p>
  </div>
  <div class="feature" style="left:607px;top:437px">
    <div class="icon"><svg width="40" height="40" viewBox="0 0 40 40" fill="none" stroke="#333" stroke-width="1.6"><path d="M20 31s-11-6.5-11-14a5.5 5.5 0 0 1 11-1.5A5.5 5.5 0 0 1 31 17c0 7.5-11 14-11 14z"/><path d="M9 20h6l2-4 3 7 2-3h9"/></svg></div>
    <h3>Save on medications</h3>
    <p>We offer deeply discounted wholesale price medications for our members at pharmacy on site.</p>
  </div>
  <div class="feature" style="left:828px;top:437px">
    <div class="icon"><svg width="40" height="40" viewBox="0 0 40 40" fill="none" stroke="#333" stroke-width="1.6"><circle cx="20" cy="14" r="6"/><path d="M9 32c0-6 5-10 11-10s11 4 11 10z"/></svg></div>
    <h3>No middle man</h3>
    <p>We don't bill any insurance plans so decisions about your healthcare will be made by you and Dr. Halvorsen, without the impersonal management that comes from third-party payers.</p>
  </div>
</section>

<div class="photo" role="img" aria-label="Group of friends embracing in a field at sunset, seen from behind"></div>

<h2 class="abs center h2" style="top:2056px">Our pricing is simple, transparent and affordable.</h2>
<p class="abs center sub" style="top:2100px;font-size:18px">Membership Plan $80/mo, plus a one-time $99 enrollment fee.</p>

<ul class="perks">
  <li><svg class="tick" viewBox="0 0 16 16"><circle cx="8" cy="8" r="8" fill="var(--tick)"/><path d="M4.5 8.3l2.3 2.2 4.7-4.8" stroke="#fff" stroke-width="1.8" fill="none"/></svg>Includes all appointments, no co-pay</li>
  <li><svg class="tick" viewBox="0 0 16 16"><circle cx="8" cy="8" r="8" fill="var(--tick)"/><path d="M4.5 8.3l2.3 2.2 4.7-4.8" stroke="#fff" stroke-width="1.8" fill="none"/></svg>Relaxed, unrushed visits</li>
  <li><svg class="tick" viewBox="0 0 16 16"><circle cx="8" cy="8" r="8" fill="var(--tick)"/><path d="M4.5 8.3l2.3 2.2 4.7-4.8" stroke="#fff" stroke-width="1.8" fill="none"/></svg>Direct communication with your doctor via phone, email, video chat 24/7</li>
  <li><svg class="tick" viewBox="0 0 16 16"><circle cx="8" cy="8" r="8" fill="var(--tick)"/><path d="M4.5 8.3l2.3 2.2 4.7-4.8" stroke="#fff" stroke-width="1.8" fill="none"/></svg>Convenient online scheduling (no need to call during business hours)</li>
  <li><svg class="tick" viewBox="0 0 16 16"><circle cx="8" cy="8" r="8" fill="var(--tick)"/><path d="M4.5 8.3l2.3 2.2 4.7-4.8" stroke="#fff" stroke-width="1.8" fill="none"/></svg>Wholesale price for labs and medications</li>
</ul>
<a href="#" class="btn">LEARN MORE ABOUT US</a>
<div class="clock-art" role="img" aria-label="Illustration of a wall clock with a gold dollar coin"></div>

<footer class="site-footer">
  <div class="fcol" style="left:172px">
    <h4><svg width="16" height="18" viewBox="0 0 16 18" fill="none" stroke="#777" stroke-width="1.4"><path d="M8 17s-6-6-6-10a6 6 0 0 1 12 0c0 4-6 10-6 10z"/><circle cx="8" cy="7" r="2"/></svg>Contact Us</h4>
    Larkfieldid<br>Lorem iSum Dummt67<br>Westbury &nbsp;&nbsp;&nbsp; dummy782<br>WB4 7QX
  </div>
  <div class="fcol" style="left:384px">
    <h4><svg width="18" height="14" viewBox="0 0 18 14" fill="none" stroke="#777" stroke-width="1.4"><rect x="1" y="1" width="16" height="12"/><path d="M1 1l8 7 8-7"/></svg>Email</h4>
    info@larkfieldid.com
    <h4 style="margin-top:22px"><svg width="16" height="16" viewBox="0 0 16 16" fill="none" stroke="#777" stroke-width="1.4"><path d="M3 1h3l1.5 4-2 1.5a9 9 0 0 0 4 4l1.5-2 4 1.5v3a1 1 0 0 1-1 1A14 14 0 0 1 2 2a1 1 0 0 1 1-1z"/></svg>Phone</h4>
    01632 555014
  </div>
  <div class="fcol" style="left:604px">
    <h4>Quick Links</h4>
    Sed ut perspiciatis<br>H iste natus error sit<br>Gptatem accusantiu<br>Rotam rem aperiam
  </div>
  <div class="brand"><span class="brand-dot"></span><span class="brand-name"><span class="word">Larkfield</span>Infectious Disease Specialists</span></div>
  <div class="frule"></div>
  <p class="copy">© 2019 All rights reserved.Terms of Use &nbsp;&nbsp;| &nbsp;&nbsp;Privacy Policy</p>
  <div class="socials"><span style="background:#3b5b98"></span><span style="background:#3aa4e0"></span><span style="background:#1f6ea8"></span><span style="background:#e0413a"></span></div>
  <span class="ver">C4</span>
</footer>

</body>
</html>
```